Guitar parts retail packaging

I have 2 boxes I need designed. This will be for my guitar parts. They are going to be thick cardstock type paper box, with a foam insert to secure the items. Matte finish with silver foil printing is sort of where im headed, but Im open to other beautiful design. The boxes will need to have a window on top of the box to show the product inside. Color scheme Im thinking with is Black with red, white and Silver foil printing. Unless you come up with something nicer, im open to that. But my business cards and some stickers are those colors.
2 different size boxes, but they can be the same basic design, modified for 2 different sizes. They will open at the front, and the lid will lift, hinged at the top back edge. (Please see purple box in picture for example for how box will work). Both boxes will have a window on top to showcase product in the box. One of the sides, (2" X 1.25") will be left a solid color, grey or other so I can put a product sticker on that side to designate what type of product is in the box. So you are really just designing the top (With window), front, back, and 1 side. Maybe something clever on the bottom but if thats blank thats fine.
LARGE BOX:
5.25 wide (Left to right)
2” deep (Front to back)
1.25” tall (Top to bottom)
SMALL BOX:
2” Wide (Left to right)
2” Deep (Front to back)
Please see Business card and sticker in picture for color scheme Im thinking. ( I am open to other colors and designs as well)

Target Market(s)

Musicians, Rockers, tattoo junkies, general badasses.

Industry/Entity Type

Guitar industry. Rock & Rollers

Font styles to use
Other font styles liked:
• I use a font called Morpheus for my logo. Also Times New Roman, maybe Copperplate? Or something more creative? Im open as long as it fits.

Colors
EB3D1F
EC4F4E
F09395
F8D3D4
FCEDEE

Requirements
Must have
• My Company name and logo (Brackenmoor Goods). Also slogan-
Nice to have
• Please see general aesthetic in sticker and biz card.
Should not have
• No horror themes, keep it cool and classy. (Even though logo is a skull). And please no pictures of guitars on the box. You might add a pic of 1 type of guitar, but the parts inside might not fit that guitar pictured on the box.

```html
<!DOCTYPE html>
<html lang="en">
<head>
<meta charset="utf-8">
<title>Brackenmoor Goods – Long Box Artwork</title>
<link rel="stylesheet" href="https://fonts.googleapis.com/css2?family=Cinzel:wght@500&display=swap">
<style>
  :root {
    --backdrop: #d4d4d4;
    --damask-black: #1b1b1b;
    --damask-red: #8e0c0f;
    --damask-white: #ebebeb;
    --window-fill: #efefef;
    --window-edge: #b9b9b9;
    --notch: #151515;
    --foil-silver: #d2d2d2;
    --label-white: #f4f4f4;
  }
  * { margin: 0; padding: 0; box-sizing: border-box; }
  html, body {
    width: 1200px;
    height: 882px;
    overflow: hidden;
    background: var(--backdrop);
  }
  .artwork {
    position: absolute;
    left: 100px;
    top: 131px;
    width: 1000px;
    height: 620px;
    box-shadow: 0 14px 34px rgba(0,0,0,0.22);
    font-family: "Cinzel", "Times New Roman", serif;
  }
  /* front face: 5.25in x 1.25in */
  .front-face {
    position: absolute;
    left: 0; top: 0;
    width: 1000px; height: 238px;
    background: linear-gradient(180deg, #242424, var(--damask-black));
    display: flex;
    flex-direction: column;
    align-items: center;
    justify-content: center;
  }
  .front-face .brand-name {
    color: var(--foil-silver);
    font-weight: 500;
    font-size: 64px;
    letter-spacing: 3px;
    line-height: 1;
  }
  .front-face .slogan {
    margin-top: 14px;
    color: var(--foil-silver);
    font-weight: 500;
    font-size: 26px;
    letter-spacing: 6px;
  }
  /* top face: 5.25in x 2in */
  .top-face {
    position: absolute;
    left: 0; top: 238px;
    width: 1000px; height: 382px;
    overflow: hidden;
  }
  .damask-red {
    position: absolute;
    left: 0; top: 0;
    width: 620px; height: 100%;
    background: radial-gradient(ellipse at 40% 45%, #a31215, var(--damask-red));
  }
  .damask-white {
    position: absolute;
    left: 620px; top: 0;
    width: 380px; height: 100%;
    background: radial-gradient(ellipse at 60% 50%, #f6f6f6, var(--damask-white));
  }
  .corner-mark {
    position: absolute;
    left: 18px; top: 30px;
    width: 170px;
    text-align: center;
    color: var(--label-white);
  }
  .corner-mark .brand-name {
    display: block;
    font-weight: 500;
    font-size: 17px;
    letter-spacing: 1px;
    line-height: 1.15;
  }
  .corner-mark .slogan {
    display: block;
    margin-top: 6px;
    font-weight: 500;
    font-size: 10px;
    letter-spacing: 1.5px;
  }
  .product-window {
    position: absolute;
    left: 200px; top: 44px;
    width: 770px; height: 300px;
  }
</style>
</head>
<body>
  <main class="artwork">
    <section class="front-face" role="img" aria-label="Black damask ornament pattern behind the brand name">
      <span class="brand-name">Brackenmoor Goods</span>
      <span class="slogan">STAGE &amp; STRING CRAFT</span>
    </section>

    <section class="top-face">
      <div class="damask-red" role="img" aria-label="Deep red damask ornament pattern"></div>
      <div class="damask-white" role="img" aria-label="Light grey on white damask ornament pattern"></div>

      <div class="corner-mark">
        <span class="brand-name">Brackenmoor Goods</span>
        <span class="slogan">STAGE &amp; STRING CRAFT</span>
      </div>

      <svg class="product-window" viewBox="0 0 770 300" aria-label="Product window cut-out">
        <rect x="1" y="1" width="768" height="298" rx="38" ry="38"
              fill="var(--window-fill)" stroke="var(--window-edge)" stroke-width="2"/>
        <path d="M355 0 A30 30 0 0 0 415 0 Z" fill="var(--notch)"/>
      </svg>
    </section>
  </main>
</body>
</html>
```